Pemberlux: Smart Quotes for Wine Lovers

Hello. I am completing book of quotes for wine lovers. Need the text formatted so that it is easy to read and aesthetically pleasing...modern, clean, smart. Number the pages. The cover is complete. Book is small square. 7.5 by 7.5 inches. If you want to show me first few pages that would be awesome. Thank you!
Updates

I edited the quotes so if you downloaded first ones, please grab these ones instead, thank you! 

Target Market(s)

wine lovers. Urban. Modern.

Industry/Entity Type

Quotes

Requirements
Should not have
• No color. black and white only.

```html
<!DOCTYPE html>
<html lang="en">
<head>
<meta charset="utf-8">
<title>Pemberlux: Smart Quotes for Wine Lovers</title>
<link rel="stylesheet" href="https://fonts.googleapis.com/css2?family=Jost:wght@400&display=swap">
<style>
  :root {
    --backdrop: #d6d6d6;
    --paper: #ffffff;
    --ink: #1a1a1a;
    --rule: #2a2a2a;
    --glass-light: #e8e8e8;
    --glass-tone: #cdcdcd;
  }
  * { box-sizing: border-box; margin: 0; padding: 0; }
  html, body {
    width: 1200px;
    height: 900px;
    overflow: hidden;
    background: var(--backdrop);
    font-family: "Jost", "Futura", sans-serif;
    color: var(--ink);
  }
  .spread {
    position: absolute;
    left: 61px;
    top: 183px;
    width: 1074px;
    height: 536px;
    display: flex;
    border: 1.5px solid var(--rule);
    background: var(--paper);
  }
  .page {
    position: relative;
    width: 50%;
    height: 100%;
  }
  .page + .page { border-left: 1.5px solid var(--rule); }
  .quote {
    position: absolute;
    left: 67px;
    top: 54px;
    width: 400px;
    font-size: 26px;
    line-height: 35px;
    font-weight: 400;
  }
  .quote-author { display: block; }
  .glass-art {
    position: absolute;
    left: 236px;
    top: 213px;
    width: 66px;
    height: 170px;
    background: linear-gradient(160deg, var(--glass-light) 0%, var(--glass-tone) 100%);
  }
  .bio {
    position: absolute;
    left: 67px;
    top: 410px;
    width: 380px;
    font-size: 12px;
    line-height: 18px;
    font-weight: 400;
  }
  .bio-name { font-weight: 400; }
  .page-number {
    position: absolute;
    left: 0;
    right: 0;
    top: 496px;
    text-align: center;
    font-size: 12px;
  }
</style>
</head>
<body>
  <main class="spread">
    <section class="page">
      <p class="quote">The discovery of a good wine is increasingly better for mankind than the discovery of a new star.<span class="quote-author">– Aurelio Vantessi</span></p>
      <div class="glass-art" role="img" aria-label="Two overlapping wine glasses in light grey"></div>
      <p class="bio"><span class="bio-name">Aurelio Benedetto Vantessi</span> (1488 – 1551)<br>Tuscan Court Painter, Glassmaker, Poet, Vintner, Traveller, Botanist, Letter Writer, Collector, Teacher, Storyteller and Host.</p>
      <p class="page-number">1</p>
    </section>
    <section class="page">
      <p class="quote">Be careful to trust a person who does not like wine.<span class="quote-author">– Konrad Malden</span></p>
      <div class="glass-art" role="img" aria-label="Two overlapping wine glasses in light grey"></div>
      <p class="bio"><span class="bio-name">Konrad Albrecht Malden</span> (1809 – 1874)<br>Rhineland Essayist, Vintner, Teacher, Travel Writer, Diarist, and Keeper of a Village Tavern.</p>
      <p class="page-number">2</p>
    </section>
  </main>
</body>
</html>
```